Medical VIP club - small design

Please read the specs in a design brief attached. Also we don't have logo in a Vector format and attaching the only version we have.

Club

```html
<!DOCTYPE html>
<html lang="en">
<head>
<meta charset="utf-8">
<title>Corvana – Our Packages</title>
<link href="https://fonts.googleapis.com/css2?family=Ubuntu:wght@300;400;500;700&display=swap" rel="stylesheet">
<style>
  :root {
    --ink-dark: #1e1704;
    --brown: #6b5a41;
    --pattern: #3b2d12;
    --nav-bg: #f7f5e6;
    --nav-line: #dcd8c2;
    --paper: #e6dcc7;
    --paper-line: #cfc4ad;
    --cell: #d2d0bc;
    --cell-alt: #c4c1ad;
    --head: #c6c4b0;
    --grid-line: #ebe9dc;
    --gold: #9a7628;
    --text: #1c1606;
    --cream: #f3ecd6;
  }
  * { box-sizing: border-box; margin: 0; padding: 0; }
  html, body { width: 1200px; height: 950px; overflow: hidden; }
  body { position: relative; background: var(--brown); font-family: "Ubuntu", sans-serif; color: var(--text); }

  .top-strip { position: absolute; left: 0; top: 0; width: 1200px; height: 30px; background: var(--ink-dark); }
  .pattern-band { position: absolute; left: 0; top: 188px; width: 1200px; height: 367px;
    background: linear-gradient(180deg, #3f3014, #34280e); }
  .footer { position: absolute; left: 0; top: 831px; width: 1200px; height: 119px; background: var(--ink-dark); }

  .brand { position: absolute; display: flex; align-items: center; gap: 10px; font-weight: 500; letter-spacing: 0.5px; }
  .brand .dot { width: 26px; height: 26px; border-radius: 50%; }
  .brand--header { left: 146px; top: 66px; font-size: 38px; color: var(--cream); }
  .brand--header .dot { background: var(--cream); }
  .brand--footer { left: 160px; top: 862px; font-size: 27px; color: #4a3c1c; }
  .brand--footer .dot { width: 20px; height: 20px; background: #4a3c1c; }

  .phone { position: absolute; left: 851px; top: 66px; font-size: 28px; font-weight: 300; color: var(--cream); letter-spacing: 0.5px; }

  .nav-bar { position: absolute; left: 114px; top: 143px; width: 960px; height: 38px; }
  .nav-bar svg { position: absolute; left: 0; top: 0; }
  .nav { position: absolute; left: 270px; top: 0; height: 38px; display: flex; list-style: none; }
  .nav li { height: 38px; display: flex; align-items: center; justify-content: center; font-size: 15px; border-right: 1px solid var(--nav-line); }
  .nav li.current { background: var(--ink-dark); color: var(--cream); height: 49px; margin-top: -11px; padding-top: 11px; }

  .panel { position: absolute; left: 114px; top: 181px; width: 960px; height: 612px; }
  .panel-head { position: absolute; left: 0; top: 0; width: 960px; height: 106px; background: var(--ink-dark); }
  .panel-title { position: absolute; left: 36px; top: 40px; font-size: 28px; font-weight: 300; color: var(--cream); }

  .col-head { position: absolute; top: 59px; width: 240px; height: 47px; background: var(--head); border-radius: 4px 4px 0 0;
    display: flex; align-items: center; justify-content: center; font-size: 22px; border-right: 1px solid var(--ink-dark); }

  .labels { position: absolute; left: 0; top: 106px; width: 238px; height: 506px; background: linear-gradient(135deg, #ece3d0, #e2d7c0); }
  .label { position: absolute; left: 0; width: 238px; height: 48px; display: flex; align-items: center; justify-content: center;
    font-size: 16px; border-bottom: 1px solid var(--paper-line); }
  .label--cost { height: auto; border: 0; top: 360px; font-size: 27px; font-weight: 700; padding-top: 8px; }

  .col { position: absolute; top: 106px; width: 240px; height: 506px; background: var(--cell); }
  .col--alt-price .price-area { background: var(--cell-alt); }
  .cell { height: 48px; border-bottom: 1px solid var(--grid-line); border-right: 1px solid var(--grid-line); display: flex; align-items: center; justify-content: center; }
  .cell svg { width: 24px; height: 24px; }
  .col--mid .cell { background: var(--cell-alt); }
  .price-area { height: 170px; display: flex; flex-direction: column; align-items: center; border-right: 1px solid var(--grid-line); }
  .price { font-size: 28px; font-weight: 700; margin-top: 26px; }
  .select-btn { margin-top: 24px; width: 172px; height: 57px; border: 1px solid #f6f2e6; border-radius: 4px;
    background: linear-gradient(180deg, #f6f1e4, #e3d9c2); color: var(--gold); font-family: inherit; font-size: 20px; font-weight: 500;
    box-shadow: 0 1px 3px rgba(0,0,0,0.15); }

  .copyright { position: absolute; left: 333px; top: 858px; font-family: Arial, sans-serif; font-size: 12px; color: #f0ede4; }
  .social { position: absolute; left: 973px; top: 852px; display: flex; gap: 8px; }
  .social span { width: 25px; height: 25px; border-radius: 3px; background: linear-gradient(180deg, #a5a28e, #6f6c5a); }
</style>
</head>
<body>
  <div class="top-strip"></div>
  <div class="pattern-band" role="img" aria-label="Dark brown damask ornament band"></div>

  <div class="brand brand--header"><span class="dot"></span>corvana</div>
  <div class="phone">416-555-0190</div>

  <div class="nav-bar">
    <svg width="960" height="38" viewBox="0 0 960 38">
      <defs><linearGradient id="navfill" x1="0" y1="0" x2="0" y2="1"><stop offset="0" stop-color="#fbfaf0"/><stop offset="1" stop-color="#ece8d0"/></linearGradient></defs>
      <path d="M20 0 H960 V38 H0 V20 Z" fill="url(#navfill)"/>
    </svg>
    <ul class="nav">
      <li style="width:53px">Home</li>
      <li style="width:93px">About Us</li>
      <li style="width:84px">VIP Club</li>
      <li style="width:85px">Services</li>
      <li style="width:161px">Packages and Prices</li>
      <li class="current" style="width:116px">Registration</li>
      <li style="width:89px">Contacts</li>
    </ul>
  </div>

  <section class="panel">
    <div class="panel-head"></div>
    <h1 class="panel-title">Our Packages</h1>
    <div class="col-head" style="left:238px">package 1</div>
    <div class="col-head" style="left:479px">package 2</div>
    <div class="col-head" style="left:720px;border-right:0">package 3</div>

    <div class="labels">
      <div class="label" style="top:0">Option 1</div>
      <div class="label" style="top:48px">Option 2</div>
      <div class="label" style="top:96px">Option 3</div>
      <div class="label" style="top:144px">Option 4</div>
      <div class="label" style="top:192px">Option 5</div>
      <div class="label" style="top:240px">Option 6</div>
      <div class="label" style="top:288px">Option 7</div>
      <div class="label label--cost">Cost ($)</div>
    </div>

    <svg width="0" height="0" style="position:absolute">
      <symbol id="tick" viewBox="0 0 24 24"><path d="M4 12.5 L9.5 18 L20 6" fill="none" stroke="#9a7628" stroke-width="3.2" stroke-linecap="round" stroke-linejoin="round"/></symbol>
    </svg>

    <div class="col" style="left:238px">
      <div class="cell"><svg><use href="#tick"/></svg></div>
      <div class="cell"><svg><use href="#tick"/></svg></div>
      <div class="cell"><svg><use href="#tick"/></svg></div>
      <div class="cell"></div><div class="cell"></div><div class="cell"></div><div class="cell"></div>
      <div class="price-area"><div class="price">$1000</div><button class="select-btn">Select Option</button></div>
    </div>
    <div class="col col--mid col--alt-price" style="left:479px">
      <div class="cell"><svg><use href="#tick"/></svg></div>
      <div class="cell"><svg><use href="#tick"/></svg></div>
      <div class="cell"><svg><use href="#tick"/></svg></div>
      <div class="cell"><svg><use href="#tick"/></svg></div>
      <div class="cell"><svg><use href="#tick"/></svg></div>
      <div class="cell"></div><div class="cell"></div>
      <div class="price-area"><div class="price">$2000</div><button class="select-btn">Select Option</button></div>
    </div>
    <div class="col" style="left:720px">
      <div class="cell"><svg><use href="#tick"/></svg></div>
      <div class="cell"><svg><use href="#tick"/></svg></div>
      <div class="cell"><svg><use href="#tick"/></svg></div>
      <div class="cell"><svg><use href="#tick"/></svg></div>
      <div class="cell"><svg><use href="#tick"/></svg></div>
      <div class="cell"><svg><use href="#tick"/></svg></div>
      <div class="cell"><svg><use href="#tick"/></svg></div>
      <div class="price-area"><div class="price">$3000</div><button class="select-btn">Select Option</button></div>
    </div>
  </section>

  <footer class="footer"></footer>
  <div class="brand brand--footer"><span class="dot"></span>corvana</div>
  <p class="copyright">Copyright 2010 Corvana. All rights reserved.</p>
  <div class="social" aria-label="Social links"><span></span><span></span><span></span></div>
</body>
</html>
```